Business card for my new company (Accounting firm)

I need a business card for my new business Brightwell Advisory and Ledger SA. Our services are accounting, tax, audit and financial management. Our customers are small companies, start-ups and new companies. The final design has to show financial security, trust and growth. Please find our logo attached to the business card. Text for the business card: Brightwell Advisory and Ledger SA Tomas Varenholt Director and Founder Certified Accountant Tel. 022 418 57 34 tv@clairevalconseil.ch www.clairevalconseil.ch Rue des Vergières 27 1201 Geneva
Target Market(s)
Our customers are small companies, start-ups and new companies.
Industry/Entity Type
Finance And Accounting
Contact Information for Business Card
Claireval Conseil et Comptes SA
Tomas Varenholt
Directeur et Fondateur
Expert-comptable diplômé
Tél. 022 418 57 34
tv@clairevalconseil.ch
www.clairevalconseil.ch
Rue des Vergières 27
1201 Genève

```html
<!DOCTYPE html>
<html lang="fr">
<head>
<meta charset="utf-8">
<title>Claireval Conseil et Comptes SA – Carte de visite</title>
<link rel="stylesheet" href="https://fonts.googleapis.com/css2?family=Roboto:wght@400;500;700&display=swap">
<style>
  :root {
    --backdrop: #e4e5e7;
    --card: #ffffff;
    --card-back: #f4f5f6;
    --blue-deep: #1d5f93;
    --blue-mid: #2a86c6;
    --blue-light: #36a3dc;
    --ink: #2f3033;
    --ink-soft: #55585c;
    --rule: #2b6fa6;
  }
  * { box-sizing: border-box; margin: 0; padding: 0; }
  html, body {
    width: 1200px; height: 726px; overflow: hidden;
    background: var(--backdrop);
    font-family: "Roboto", Arial, sans-serif;
  }
  .sheet {
    position: relative; width: 1200px; height: 726px;
    display: flex; align-items: center; justify-content: center; gap: 60px;
  }
  .card {
    position: relative; width: 520px; height: 336px;
    background: var(--card);
    box-shadow: 0 10px 28px rgba(0,0,0,0.14), 0 2px 5px rgba(0,0,0,0.08);
    overflow: hidden;
  }
  .card--back { background: var(--card-back); }

  /* Wordmark */
  .wordmark { display: flex; align-items: center; gap: 12px; color: var(--ink); font-weight: 500; }
  .wordmark__square { width: 34px; height: 34px; background: var(--blue-mid); flex: none; }
  .wordmark__text { display: flex; flex-direction: column; line-height: 1; }
  .wordmark__name { font-size: 30px; letter-spacing: 3px; }
  .wordmark__sub { font-size: 11px; letter-spacing: 3px; margin-top: 6px; }

  .card--front .wordmark {
    position: absolute; left: 50%; top: 128px; transform: translateX(-50%);
  }
  .front-band { position: absolute; left: 0; bottom: 0; width: 100%; height: 80px; }

  .card--back .wordmark {
    position: absolute; right: 30px; top: 44px;
  }
  .card--back .wordmark__name { font-size: 24px; letter-spacing: 2px; }
  .card--back .wordmark__sub { font-size: 9px; letter-spacing: 2.4px; }
  .card--back .wordmark__square { width: 28px; height: 28px; }

  .back-rule { position: absolute; left: 0; top: 0; width: 520px; height: 336px; }

  .address {
    position: absolute; right: 30px; top: 142px; text-align: right;
    font-size: 12px; line-height: 1.45; color: var(--ink);
  }
  .person { position: absolute; left: 30px; top: 176px; }
  .person__name { font-size: 20px; font-weight: 700; color: var(--blue-deep); }
  .person__role { font-size: 10.5px; line-height: 1.4; color: var(--ink-soft); margin-top: 6px; }

  .contacts { position: absolute; left: 30px; top: 262px; list-style: none; }
  .contacts li {
    display: flex; align-items: center; gap: 10px;
    font-size: 12px; color: var(--ink); line-height: 19px;
  }
  .contacts svg { width: 12px; height: 12px; fill: var(--blue-deep); flex: none; }
</style>
</head>
<body>
<main class="sheet">

  <section class="card card--front" aria-label="Recto de la carte">
    <div class="wordmark">
      <span class="wordmark__square"></span>
      <span class="wordmark__text">
        <span class="wordmark__name">CLAIREVAL</span>
        <span class="wordmark__sub">CONSEIL ET COMPTES</span>
      </span>
    </div>
    <svg class="front-band" viewBox="0 0 520 80" preserveAspectRatio="none" aria-hidden="true">
      <polygon points="0,58 520,6 520,14 0,66" fill="var(--blue-deep)"/>
      <polygon points="0,66 520,14 520,22 0,74" fill="var(--blue-light)"/>
    </svg>
  </section>

  <section class="card card--back" aria-label="Verso de la carte">
    <svg class="back-rule" viewBox="0 0 520 336" aria-hidden="true">
      <path d="M490 128 L330 130 C 290 131, 270 165, 230 180 C 210 187, 195 188, 175 189"
            fill="none" stroke="var(--rule)" stroke-width="1"/>
    </svg>

    <div class="wordmark">
      <span class="wordmark__square"></span>
      <span class="wordmark__text">
        <span class="wordmark__name">CLAIREVAL</span>
        <span class="wordmark__sub">CONSEIL ET COMPTES</span>
      </span>
    </div>

    <p class="address">Rue des Vergières 27<br>1201 Genève</p>

    <div class="person">
      <h1 class="person__name">Tomas Varenholt</h1>
      <p class="person__role">Directeur et Fondateur<br>Expert-comptable diplômé</p>
    </div>

    <ul class="contacts">
      <li>
        <svg viewBox="0 0 12 12"><path d="M2.5 1 L4.5 1 L5.2 3.4 L4 4.4 C4.6 5.8 6.2 7.4 7.6 8 L8.6 6.8 L11 7.5 L11 9.5 C11 10.3 10.3 11 9.5 11 C5 11 1 7 1 2.5 C1 1.7 1.7 1 2.5 1 Z"/></svg>
        022 418 57 34
      </li>
      <li>
        <svg viewBox="0 0 12 12"><path d="M0.5 2.5 H11.5 V9.5 H0.5 Z M1.5 3.3 L6 6.6 L10.5 3.3 V3 H1.5 Z" fill-rule="evenodd"/></svg>
        tv@clairevalconseil.ch
      </li>
      <li>
        <svg viewBox="0 0 12 12"><circle cx="6" cy="6" r="5.2"/><path d="M1 6 H11 M6 0.8 C3.5 3.5 3.5 8.5 6 11.2 M6 0.8 C8.5 3.5 8.5 8.5 6 11.2" stroke="#fff" stroke-width="0.8" fill="none"/></svg>
        www.clairevalconseil.ch
      </li>
    </ul>
  </section>

</main>
</body>
</html>
```